Beacon Advisory Website

I currently have a website www.beaconadvisoryinc.com. We are a IT Consulting Company. Our website will pretty much tell out our services. I am looking to enhance my website and make it look more professional. Looking for very classy and Contemporary look and design for my website.

It Company

```html
<!DOCTYPE html>
<html lang="en">
<head>
<meta charset="utf-8">
<title>Beacon Advisory</title>
<link href="https://fonts.googleapis.com/css2?family=Raleway:wght@400;500;600&display=swap" rel="stylesheet">
<style>
:root{
  --navy:#0d3f86;
  --blue:#1b72c4;
  --sky:#03a7e2;
  --grey-card:#5e5e5e;
  --frame:#c8c8c8;
  --text:#4a4a4a;
  --rule:#d6d6d6;
  --footer:#efefef;
  --ink:#1d1d1d;
}
*{margin:0;padding:0;box-sizing:border-box}
html,body{width:1094px;height:1200px;overflow:hidden;background:#fff;font-family:'Raleway',sans-serif;color:var(--text)}
.page{position:relative;width:1094px;height:1200px}

.brand{position:absolute;display:flex;align-items:center;gap:8px;color:var(--navy);font-weight:600;text-transform:uppercase;line-height:1}
.brand-dot{border-radius:50%;background:var(--navy)}
.header .brand{left:68px;top:28px;font-size:20px}
.header .brand-dot{width:34px;height:34px}

.nav{position:absolute;left:381px;top:27px;width:646px;height:44px;background:var(--blue);clip-path:polygon(14px 0,100% 0,calc(100% - 14px) 100%,0 100%);display:flex;align-items:center}
.nav a{color:#fff;text-decoration:none;font-size:11.5px;font-weight:500;height:100%;display:flex;align-items:center;padding:0 16px}
.nav a.active{background:var(--navy);padding:0 17px 0 32px}

.hero{position:absolute;left:0;top:91px;width:1094px;height:553px;clip-path:polygon(0 0,100% 0,100% 395px,0 100%);
  background:radial-gradient(ellipse 260px 340px at 760px 200px,#2c2f36 0%,rgba(44,47,54,0) 100%),
  radial-gradient(ellipse 220px 180px at 560px 330px,#d9a58c 0%,rgba(217,165,140,0) 100%),
  linear-gradient(90deg,#7c7f84 0%,#b9bcc0 35%,#8e9196 65%,#5d6066 100%)}
.headline{position:absolute;left:68px;top:258px}
.headline span{display:block;width:max-content;background:rgba(60,60,60,.85);color:#fff;font-size:37px;font-weight:600;text-transform:uppercase;padding:0 8px;height:45px;line-height:46px;margin-bottom:2px}
.dots{position:absolute;left:68px;top:371px;display:flex;gap:6px}
.dots i{width:10px;height:10px;border-radius:50%;background:#fff}
.dots i:first-child{background:var(--sky)}

.card{position:absolute;top:450px;width:222px;height:291px;border:4px solid var(--frame);color:#fff;text-align:center;padding-top:14px}
.card::after{content:"";position:absolute;left:20px;right:20px;bottom:-18px;height:10px;border-radius:50%;background:radial-gradient(ellipse at center,rgba(0,0,0,.25),rgba(0,0,0,0) 70%)}
.card.consulting{left:335px;background:var(--blue)}
.card.staffing{left:570px;background:var(--sky)}
.card.offshore{left:804px;background:var(--grey-card)}
.card svg{width:52px;height:50px}
.card h3{font-size:17px;font-weight:500;line-height:20px;margin-top:10px;text-transform:uppercase}
.card p{font-size:12.6px;line-height:20px;margin:10px 14px 0}
.card .more{position:absolute;left:58px;top:234px;width:98px;height:32px;border:1.5px solid #fff;font-size:13px;font-weight:500;line-height:29px}

.divider{position:absolute;left:68px;top:816px;width:958px;height:1px;background:var(--rule)}
.divider-dot{position:absolute;left:534px;top:806px;width:22px;height:22px;border-radius:50%;background:var(--navy);box-shadow:0 0 0 8px #fff}
.welcome h2{position:absolute;left:0;width:1094px;top:849px;text-align:center;color:var(--navy);font-size:21px;font-weight:500;text-transform:uppercase}
.welcome p{position:absolute;left:68px;width:958px;top:890px;text-align:center;font-size:12.6px;line-height:22px}
.welcome .cta{position:absolute;left:478px;top:1004px;width:139px;height:37px;background:linear-gradient(#3a3a3a,var(--ink));color:#fff;font-size:12.5px;font-weight:500;text-align:center;line-height:37px}

.footer{position:absolute;left:0;top:1075px;width:1094px;height:125px;background:var(--footer);border-top:4px solid var(--sky)}
.footer .brand{left:68px;top:20px;font-size:16px}
.footer .brand-dot{width:28px;height:28px}
.copy{position:absolute;left:68px;top:76px;font-size:12.4px;color:#333}
.follow{position:absolute;left:864px;top:30px;font-size:12.4px;color:#333}
.social{position:absolute;left:864px;top:52px;display:flex;gap:7px}
.social i{width:27px;height:27px;border-radius:50%}
</style>
</head>
<body>
<div class="page">
  <header class="header">
    <div class="brand"><span class="brand-dot"></span>Beacon Advisory</div>
    <nav class="nav">
      <a class="active">HOME</a><a>COMPANY</a><a>SERVICES</a><a>SOLUTIONS</a><a>RESOURCES</a><a>CAREER</a><a>CONTACT US</a>
    </nav>
  </header>

  <section class="hero" role="img" aria-label="Businessman in a suit touching a glowing network diagram of connected people icons"></section>
  <div class="headline"><span>Lorem ipsum dolor sit amet,</span><span>etuer adipiscing elit</span></div>
  <div class="dots"><i></i><i></i><i></i><i></i></div>

  <article class="card consulting">
    <svg viewBox="0 0 52 50" fill="#fff"><circle cx="26" cy="6" r="4"/><circle cx="10" cy="12" r="4"/><circle cx="42" cy="12" r="4"/><rect x="14" y="20" width="24" height="5"/><rect x="6" y="18" width="7" height="14"/><rect x="39" y="18" width="7" height="14"/><rect x="22" y="11" width="8" height="8"/><rect x="17" y="25" width="4" height="20"/><rect x="31" y="25" width="4" height="20"/><rect x="24" y="25" width="4" height="14"/></svg>
    <h3>Consulting<br>Services</h3>
    <p>Beacon Advisory has certified professional consultants to work with you to help increase the business by providing IT services ...</p>
    <div class="more">Read More</div>
  </article>
  <article class="card staffing">
    <svg viewBox="0 0 52 50" fill="#fff"><circle cx="26" cy="6" r="4"/><circle cx="15" cy="9" r="3.5"/><circle cx="37" cy="9" r="3.5"/><circle cx="6" cy="16" r="3.5"/><circle cx="46" cy="16" r="3.5"/><rect x="21" y="12" width="10" height="10" rx="2"/><rect x="2" y="22" width="10" height="10" rx="2"/><rect x="40" y="22" width="10" height="10" rx="2"/><ellipse cx="26" cy="32" rx="16" ry="6"/><circle cx="26" cy="40" r="4"/><rect x="19" y="44" width="14" height="6" rx="2"/></svg>
    <h3>Staff<br>Augmentation</h3>
    <p>For years Beacon Advisory as been offering our customers the ability to augment their existing staff ..</p>
    <div class="more">Read More</div>
  </article>
  <article class="card offshore">
    <svg viewBox="0 0 52 50" fill="#fff"><circle cx="18" cy="34" r="11"/><circle cx="18" cy="34" r="4.5" fill="#5e5e5e"/><rect x="16" y="19" width="4" height="30"/><rect x="3" y="32" width="30" height="4"/><path d="M30 8l5-5 6 2-4 4 1 4 4 1 4-4 2 6-5 5-5 0-14 14-4-4 14-14z"/></svg>
    <h3>Offshore<br>Development</h3>
    <p>Our Offshore development model has a unique distinction of providing efficient software solutions...</p>
    <div class="more">Read More</div>
  </article>

  <div class="divider"></div>
  <div class="divider-dot"></div>
  <section class="welcome">
    <h2>Welcome to Beacon Advisory</h2>
    <p>Today's IT market is a dynamic, fast-paced industry, with ever-increasing demands. Meeting these demands for over 25 years, Beacon Advisory maintains a global presence, aggressively recruiting expertly qualified IT and Management Professionals from around the world and cultivating key partnerships with corporations to understand their business models end-to-end, with a goal of delivering exceptional client service and ensuring a consistent delivery of the talent needed to drive results.</p>
    <div class="cta">READ MORE</div>
  </section>

  <footer class="footer">
    <div class="brand"><span class="brand-dot"></span>Beacon Advisory</div>
    <div class="copy">Copyright © 2016. All Right Reserved. Privacy Policy</div>
    <div class="follow">Follow Us:</div>
    <div class="social">
      <i style="background:#1e4e9c"></i><i style="background:#1d9be0"></i><i style="background:#1b73b8"></i><i style="background:#3d3d3d"></i><i style="background:#f7931e"></i>
    </div>
  </footer>
</div>
</body>
</html>
```